Executive Business Card for Healthcare Company [Need Today]

I need a business card design for a healthcare company. The only branding the company has thus far is a logo. The cards will be utilized by company executives. The design I envision will be vibrant and appealing but with a corporate feel. They shouldn't be too casual or playful. I would like to complete this project TODAY if possible.

Target Market(s)

Healthcare vendors, other executives in healthcare and pharmaceuticals

Industry/Entity Type

Pharmaceutical

Contact Information for Business Card

See attachment

Font styles to use
Serif
Sans Serif

Colors

Designer to choose colors to be used in the design.

```html
<!DOCTYPE html>
<html lang="en">
<head>
<meta charset="utf-8">
<title>Corvane Therapeutics – Business Card</title>
<link href="https://fonts.googleapis.com/css2?family=Open+Sans:wght@400;700&display=swap" rel="stylesheet">
<style>
  :root {
    --page-bg: #e9ebec;
    --teal: #37bfc6;
    --teal-faint: rgba(20, 120, 128, 0.18);
    --green: #46aa78;
    --white: #ffffff;
    --card-shadow: 0 12px 28px rgba(0, 0, 0, 0.18);
  }
  * { box-sizing: border-box; margin: 0; padding: 0; }
  html, body {
    width: 1200px; height: 1000px; overflow: hidden;
    background: var(--page-bg);
    font-family: "Open Sans", Arial, sans-serif;
  }
  .canvas { position: relative; width: 1200px; height: 1000px; }

  .card {
    position: absolute;
    width: 540px; height: 310px;
    border-radius: 20px;
    overflow: hidden;
    box-shadow: var(--card-shadow);
  }

  /* Shared brand lockup */
  .brand { position: absolute; display: flex; align-items: center; }
  .brand-mark { border-radius: 50%; flex: none; }
  .brand-rule { width: 1px; align-self: stretch; flex: none; }
  .brand-name { font-weight: 400; letter-spacing: 0.5px; line-height: 1.1; white-space: nowrap; }
  .brand-name span { display: block; }

  /* Front */
  .card-front { left: 110px; top: 120px; background: var(--teal); }
  .card-front .faint-ring {
    position: absolute; left: 300px; top: -20px;
    width: 300px; height: 300px; border-radius: 50%;
    border: 6px solid var(--teal-faint);
  }
  .card-front .brand { left: 70px; top: 105px; height: 100px; gap: 18px; }
  .card-front .brand-mark { width: 100px; height: 100px; border: 3px solid var(--white); }
  .card-front .brand-rule { background: rgba(255,255,255,0.7); }
  .card-front .brand-name { color: var(--white); font-size: 30px; }

  /* Back */
  .card-back { left: 550px; top: 540px; background: var(--white); }
  .card-back .arcs { position: absolute; inset: 0; }
  .card-back .brand { left: 34px; top: 196px; height: 62px; gap: 11px; }
  .card-back .brand-mark { width: 62px; height: 62px; border: 2px solid var(--teal); }
  .card-back .brand-rule { background: #c9c9c9; }
  .card-back .brand-name { color: var(--teal); font-size: 17px; }

  .contact {
    position: absolute; right: 26px; top: 40px;
    width: 240px; text-align: right; color: var(--white);
  }
  .contact-name { font-weight: 700; font-size: 18px; letter-spacing: 0.5px; }
  .contact-title { font-size: 12px; margin-bottom: 22px; }
  .contact-address { font-size: 12.5px; line-height: 1.35; margin-bottom: 18px; }
  .contact-line { font-size: 12.5px; line-height: 1.45; display: flex; justify-content: flex-end; align-items: center; gap: 6px; }
  .contact-line svg { width: 11px; height: 11px; flex: none; }
</style>
</head>
<body>
<main class="canvas">

  <section class="card card-front" aria-label="Business card front">
    <div class="faint-ring"></div>
    <div class="brand">
      <span class="brand-mark"></span>
      <span class="brand-rule"></span>
      <span class="brand-name"><span>Corvane</span><span>Therapeutics</span></span>
    </div>
  </section>

  <section class="card card-back" aria-label="Business card back">
    <svg class="arcs" width="540" height="310" viewBox="0 0 540 310" aria-hidden="true">
      <circle cx="470" cy="150" r="238" fill="var(--teal)"/>
      <circle cx="478" cy="150" r="228" fill="var(--white)"/>
      <circle cx="486" cy="148" r="222" fill="var(--green)"/>
    </svg>

    <div class="brand">
      <span class="brand-mark"></span>
      <span class="brand-rule"></span>
      <span class="brand-name"><span>Corvane</span><span>Therapeutics</span></span>
    </div>

    <div class="contact">
      <p class="contact-name">MARTIN HALE</p>
      <p class="contact-title">Senior Director of Marketing</p>
      <p class="contact-address">Corvane Therapeutics, LLC<br>118 Linden Grove Avenue<br>Fairview, GA 30990</p>
      <p class="contact-line">
        <svg viewBox="0 0 12 12"><path d="M2.5 1 L4.5 1 L5.3 3.6 L4 4.6 Q5 7 7.4 8 L8.4 6.7 L11 7.5 L11 9.5 Q11 11 9.5 11 Q1 10.5 1 2.5 Q1 1 2.5 1Z" fill="var(--white)"/></svg>
        555-210-4417 (Office)
      </p>
      <p class="contact-line">555-382-6051 (Cell)</p>
      <p class="contact-line">
        <svg viewBox="0 0 12 12"><rect x="0.5" y="2" width="11" height="8" rx="1" fill="var(--white)"/><path d="M1 2.6 L6 6.5 L11 2.6" fill="none" stroke="var(--green)" stroke-width="1.1"/></svg>
        mhale@corvanerx.com
      </p>
    </div>
  </section>

</main>
</body>
</html>
```